New Website for World Wide Charity (KOLVAN)

We need a dynamic web design for our brand new charity organisation that will be working worldwide. We will be funded by donations so need to attract people to donate.

What We Do
We work to optimise the wellbeing of the planet, the animals and all that live within. Our slogan is Achieving Vibrational Equilibrium.

We have included a Powerpoint document which may help you understand what we need, it is just an idea for structure and style, it is not set in stone so feel free to be as creative as you like!
Updates

Designs look the same

Target Market(s)

Adults 18+ with an interest in animal, environmental. Businesses that may like to support our natural world or already support our natural world.

Number of Pages Required

3 page

Colors

Designer to choose colors to be used in the design.

Requirements
Must have
• We need the website to be easy to use and understand.

Web pages will be Home, What We Do, Who We Are, Success Stories, What You Can Do (Blog section), Seek Help, Donate, Join.
Nice to have
• Natural feel, easy to navigate, Ideally the website will look natural and organic.

Natural colours, blues, greens, sand, gold, brown, grey, silver, Orange and yellow for impact.
Should not have
• Should not have a dark coloured theme.

```html
<!DOCTYPE html>
<html lang="en">
<head>
<meta charset="utf-8">
<title>KOLVAN – Achieving Vibrational Equilibrium</title>
<link href="https://fonts.googleapis.com/css2?family=Lato:wght@400;700;900&display=swap" rel="stylesheet">
<style>
:root{
  --teal:#3a9e97;
  --teal-light:#c9e6e3;
  --ink:#1c1c1c;
  --text:#444;
  --muted:#777;
  --footer:#1d1f21;
  --footer-text:#d8d8d8;
  --white:#fff;
}
*{margin:0;padding:0;box-sizing:border-box}
html,body{width:1200px;height:2964px;overflow:hidden;background:var(--white);font-family:'Lato',sans-serif;color:var(--text)}
.page{position:relative;width:1200px;height:2964px}
.abs{position:absolute}

/* header */
.brand{left:52px;top:8px;width:84px;height:84px;border-radius:50%;border:2px solid var(--teal);display:flex;align-items:center;justify-content:center;font-weight:900;font-size:15px;color:var(--teal);letter-spacing:1px}
.nav{left:240px;top:48px;display:flex;gap:34px;font-size:14px;color:var(--ink)}
.nav a{color:inherit;text-decoration:none}
.nav .current{color:var(--teal);font-weight:700}
.search{left:1070px;top:36px}

/* hero */
.hero{left:0;top:104px;width:1200px;height:556px;background:linear-gradient(180deg,#cfc3dc 0%,#a88fbf 35%,#8f79ad 55%,#c9bfd9 75%,#e7e2ec 100%)}
.hero-copy{left:0;top:262px;width:1200px;text-align:center;color:var(--white)}
.hero-copy h1{font-size:38px;font-weight:900;letter-spacing:1px}
.hero-copy p{font-size:18px;font-weight:700;margin-top:18px}
.btn{display:inline-block;background:var(--teal);color:var(--white);font-weight:700;font-size:13px;letter-spacing:.5px;padding:12px 22px;text-transform:uppercase}
.hero-copy .btn{margin-top:26px;font-size:15px;padding:14px 26px}
.arrow{top:366px}
.dots{left:560px;top:592px;display:flex;gap:8px}
.dots span{width:10px;height:10px;border-radius:50%;background:rgba(255,255,255,.6)}
.dots span.on{background:var(--teal)}

/* pillars */
.pillar{width:330px;height:340px;background:var(--white);box-shadow:0 2px 12px rgba(0,0,0,.18);text-align:center;padding-top:30px}
.pillar h3{color:var(--teal);font-weight:400;font-size:16px;margin-top:14px}
.pillar p{font-size:13px;line-height:1.55;margin:14px 34px 0}
.pillar .btn{margin-top:18px}

/* section heading */
.section-title{left:0;top:1205px;width:1200px;text-align:center;font-size:32px;font-weight:900;color:var(--ink)}

/* feature rows */
.feature-media{width:440px;height:330px}
.media-back{background:var(--teal-light);transform:rotate(-4deg)}
.feature-text h2{font-size:30px;font-weight:900;color:var(--ink);letter-spacing:1px}
.feature-text p{font-size:13.5px;line-height:1.65;margin-top:18px;width:470px}
.read-more{display:flex;align-items:center;gap:12px;margin-top:28px;color:var(--teal);font-size:14px;font-weight:700}
.read-more i{width:18px;height:18px;border-radius:50%;background:var(--teal);display:inline-flex;align-items:center;justify-content:center}

/* footer */
.footer{left:0;top:2600px;width:1200px;height:364px;background:var(--footer);color:var(--footer-text)}
.footer .brand{left:90px;top:62px;width:90px;height:90px;border-color:var(--footer-text);color:var(--footer-text);position:absolute}
.footer-about{left:90px;top:178px;width:310px;font-size:13px;line-height:1.6}
.footer-col{top:80px;font-size:13px;line-height:2.1}
.footer-col h4{font-size:14px;font-weight:700;color:var(--white);margin-bottom:12px}
.footer-base{top:330px;font-size:12px}
</style>
</head>
<body>
<div class="page">

  <!-- header -->
  <div class="abs brand">KOLVAN</div>
  <nav class="abs nav">
    <a class="current" href="#">Home</a>
    <a href="#">What We Do</a>
    <a href="#">Who We Are</a>
    <a href="#">Success Stories</a>
    <a href="#">What You Can Do</a>
    <a href="#">Donate and Join</a>
  </nav>
  <svg class="abs search" width="34" height="34" viewBox="0 0 34 34" aria-label="Search"><circle cx="14" cy="14" r="10" fill="none" stroke="#555" stroke-width="2.5"/><line x1="21.5" y1="21.5" x2="31" y2="31" stroke="#555" stroke-width="2.5"/></svg>

  <!-- hero -->
  <div class="abs hero" role="img" aria-label="Violet mountain landscape reflected in a lake with flying birds"></div>
  <div class="abs hero-copy">
    <h1>HELP RAISE WORLD VIBRATION</h1>
    <p>Achieving Vibrational Equilibrium</p>
    <span class="btn">Make a difference</span>
  </div>
  <svg class="abs arrow" style="left:14px" width="18" height="34" viewBox="0 0 18 34"><polyline points="15,3 3,17 15,31" fill="none" stroke="#fff" stroke-width="3"/></svg>
  <svg class="abs arrow" style="left:1168px" width="18" height="34" viewBox="0 0 18 34"><polyline points="3,3 15,17 3,31" fill="none" stroke="#fff" stroke-width="3"/></svg>
  <div class="abs dots"><span class="on"></span><span></span><span></span></div>

  <!-- pillars -->
  <div class="abs pillar" style="left:80px;top:745px">
    <svg width="60" height="56" viewBox="0 0 60 56"><rect x="6" y="4" width="48" height="48" rx="6" fill="none" stroke="#3a9e97" stroke-width="2.5"/><path d="M30 42V22M30 30c-8 0-12-6-12-12 8 0 12 5 12 12zM30 26c0-7 5-12 12-12 0 7-4 12-12 12z" fill="none" stroke="#3a9e97" stroke-width="2.5"/></svg>
    <h3>Environment</h3>
    <p>Lorem ipsum dolor sit, consectetur adipiscing elit, sed do eiusmod tempor incididunt ut labore et dolore magna.</p>
    <span class="btn">Find out more</span>
  </div>
  <div class="abs pillar" style="left:435px;top:790px">
    <svg width="60" height="56" viewBox="0 0 60 56"><g fill="none" stroke="#3a9e97" stroke-width="2.5"><ellipse cx="30" cy="38" rx="11" ry="9"/><circle cx="16" cy="24" r="5"/><circle cx="25" cy="14" r="5"/><circle cx="35" cy="14" r="5"/><circle cx="44" cy="24" r="5"/></g></svg>
    <h3>Animal</h3>
    <p>Lorem ipsum dolor sit, consectetur adipiscing elit, sed do eiusmod tempor incididunt ut labore et dolore magna.</p>
    <span class="btn">Find out more</span>
  </div>
  <div class="abs pillar" style="left:780px;top:740px">
    <svg width="60" height="56" viewBox="0 0 60 56"><g fill="none" stroke="#3a9e97" stroke-width="2.5"><circle cx="30" cy="12" r="7"/><path d="M18 30c4-8 20-8 24 0M14 44c6-6 26-6 32 0M30 22v14"/></g></svg>
    <h3>Human</h3>
    <p>Lorem ipsum dolor sit, consectetur adipiscing elit, sed do eiusmod tempor incididunt ut labore et dolore magna.</p>
    <span class="btn">Find out more</span>
  </div>

  <h2 class="abs section-title">OUR VIBRATIONAL EQUILIBRIUM</h2>

  <!-- environment -->
  <div class="abs feature-media media-back" style="left:100px;top:1370px"></div>
  <div class="abs feature-media" style="left:90px;top:1355px;background:linear-gradient(135deg,#e9d46a 0%,#8fbf3e 45%,#3f7d2a 100%)" role="img" aria-label="Hands holding a small tree with soil"></div>
  <div class="abs feature-text" style="left:640px;top:1410px">
    <h2>ENVIRONMENT</h2>
    <p>Lorem ipsum dolor sit amet, consectetur adipiscing elit, sed do eiusmod tempor incididunt ut labore et dolore magna aliqua. Ut enim ad minim veniam, quis nostrud exercitation ullamco laboris nisi ut aliquip ex ea commodo consequat. Duis aute irure dolor in reprehenderit in voluptate.</p>
    <div class="read-more">Read More <i><svg width="8" height="10" viewBox="0 0 8 10"><polyline points="2,1 6,5 2,9" fill="none" stroke="#fff" stroke-width="2"/></svg></i></div>
  </div>

  <!-- animal -->
  <div class="abs feature-text" style="left:85px;top:1850px">
    <h2>ANIMAL</h2>
    <p>Lorem ipsum dolor sit amet, consectetur adipiscing elit, sed do eiusmod tempor incididunt ut labore et dolore magna aliqua. Ut enim ad minim veniam, quis nostrud exercitation ullamco laboris nisi ut aliquip ex ea commodo consequat. Duis aute irure dolor in reprehenderit in voluptate.</p>
    <div class="read-more">Read More <i><svg width="8" height="10" viewBox="0 0 8 10"><polyline points="2,1 6,5 2,9" fill="none" stroke="#fff" stroke-width="2"/></svg></i></div>
  </div>
  <div class="abs feature-media media-back" style="left:680px;top:1785px;transform:rotate(4deg)"></div>
  <div class="abs feature-media" style="left:665px;top:1770px;background:linear-gradient(160deg,#6f8a4a 0%,#5a4a32 50%,#8a7a5a 100%)" role="img" aria-label="Brown bear standing in a grassy forest"></div>

  <!-- human -->
  <div class="abs feature-media media-back" style="left:100px;top:2195px"></div>
  <div class="abs feature-media" style="left:90px;top:2180px;background:linear-gradient(180deg,#d9e7c5 0%,#9cc173 50%,#6d9a45 100%)" role="img" aria-label="Person meditating cross-legged on grass in a park"></div>
  <div class="abs feature-text" style="left:640px;top:2240px">
    <h2>HUMAN</h2>
    <p>Lorem ipsum dolor sit amet, consectetur adipiscing elit, sed do eiusmod tempor incididunt ut labore et dolore magna aliqua. Ut enim ad minim veniam, quis nostrud exercitation ullamco laboris nisi ut aliquip ex ea commodo consequat. Duis aute irure dolor in reprehenderit in voluptate.</p>
    <div class="read-more">Read More <i><svg width="8" height="10" viewBox="0 0 8 10"><polyline points="2,1 6,5 2,9" fill="none" stroke="#fff" stroke-width="2"/></svg></i></div>
  </div>

  <!-- footer -->
  <footer class="abs footer">
    <div class="brand">KOLVAN</div>
    <p class="abs footer-about">Lorem ipsum dolor amet, consectetur adipiscing elit,do eiusmod tempor incididunt ut labore et dolore magna.</p>
    <div class="abs footer-col" style="left:495px">
      <h4>Get Involved</h4>
      <div>Join Us</div><div>Fundraise</div><div>Donate</div><div>Shop</div>
    </div>
    <div class="abs footer-col" style="left:735px">
      <h4>Get Help</h4>
      <div>Contact Us</div><div>Media</div>
    </div>
    <div class="abs footer-col" style="left:950px">
      <h4>Legal</h4>
      <div>Terms and Conditions</div><div>Cookies</div><div>Privacy Policy</div>
    </div>
    <div class="abs footer-base" style="left:90px">Charity Number: 1234567</div>
    <div class="abs footer-base" style="left:735px">©Copyright 2023 Kolvan All right reserved.</div>
  </footer>

</div>
</body>
</html>
```